Redesign current business card for food company

i would like to redesign my business card. our company is food company, our product range from chips, juices, milk and etc (mostly dried food stuff).
I want o keep same logo but , the rest is open to new design.
you can check at our website about our company www.orvelpantry.com

Target Market(s)

most of food company

Industry/Entity Type

Business

Contact Information for Business Card

I want to keep more to blue color...

Colors
3176b5
abd036

Requirements
Must have
• our old logo
Nice to have
• we do not mind to have nice material on bus card in order to accomplish nice design. for example: using spot uv, embossed and etc.

```html
<!DOCTYPE html>
<html lang="en">
<head>
<meta charset="utf-8">
<title>Orvel Pantry – Business Card</title>
<link rel="stylesheet" href="https://fonts.googleapis.com/css2?family=Lato:wght@400;700;900&display=swap">
<style>
  :root {
    --bg: #e9e6e2;
    --card-white: #fbfbfa;
    --leaf-green: #27c95a;
    --brand-blue: #1f3fa6;
    --brand-blue-light: #3176b5;
    --brand-green: #4cb83a;
    --text-dark: #3a3a3a;
    --rule: #cfcfcf;
  }
  * { margin: 0; padding: 0; box-sizing: border-box; }
  html, body { width: 1200px; height: 794px; overflow: hidden; }
  body {
    background: var(--bg);
    font-family: "Lato", Arial, sans-serif;
    position: relative;
  }
  .card {
    position: absolute;
    left: 300px;
    width: 600px;
    height: 343px;
    box-shadow: 0 2px 6px rgba(0,0,0,0.12);
    overflow: hidden;
  }
  .card--back { top: 34px; background: var(--leaf-green); }
  .card--back .pattern-area { position: absolute; inset: 0; background: linear-gradient(135deg, #2fd063, #22bf52); }
  .card--front { top: 417px; background: var(--card-white); }

  .brand-name {
    position: absolute; right: 42px; top: 38px;
    font-size: 60px; font-weight: 700; color: var(--brand-blue-light);
    letter-spacing: -1px;
  }
  .mobile {
    position: absolute; right: 30px; top: 128px;
    display: flex; align-items: center; gap: 8px;
    font-size: 14px; color: var(--text-dark);
  }
  .rule { position: absolute; height: 1px; background: var(--rule); }
  .rule--right { left: 250px; right: 22px; top: 156px; }
  .rule--left { left: 22px; width: 300px; top: 232px; }

  .address {
    position: absolute; right: 30px; top: 168px;
    text-align: right; font-size: 14px; line-height: 19px; color: var(--text-dark);
  }
  .address .website { color: var(--brand-blue); font-weight: 700; letter-spacing: 0.3px; }

  .person { position: absolute; left: 26px; top: 190px; }
  .person .name { font-size: 19px; font-weight: 900; color: var(--brand-blue); }
  .person .role { font-size: 13px; font-weight: 700; color: var(--brand-green); margin-top: 2px; }

  .contacts { position: absolute; left: 36px; top: 244px; list-style: none; }
  .contacts li {
    display: flex; align-items: center; gap: 8px;
    font-size: 14.5px; color: var(--text-dark); height: 21px;
  }
  .contacts svg { width: 13px; height: 13px; fill: var(--brand-blue); }

  .base-band { position: absolute; left: 0; bottom: 0; width: 600px; height: 40px; }
</style>
</head>
<body>
  <section class="card card--back">
    <div class="pattern-area" role="img" aria-label="Repeating leaf pattern in light and dark green"></div>
  </section>

  <section class="card card--front">
    <div class="brand-name">Orvel</div>

    <div class="mobile">
      <span>626 555 0187</span>
      <svg width="10" height="15" viewBox="0 0 10 15" aria-hidden="true">
        <rect x="0.75" y="0.75" width="8.5" height="13.5" rx="1.5" fill="none" stroke="#1f3fa6" stroke-width="1.5"/>
        <rect x="3.5" y="11" width="3" height="1.2" fill="#1f3fa6"/>
      </svg>
    </div>
    <div class="rule rule--right"></div>

    <div class="address">
      <div>1420 Maple St.</div>
      <div>Fairview CA 91700</div>
      <div class="website">www.orvelpantry.com</div>
    </div>

    <div class="person">
      <div class="name">Daniel Hartanto</div>
      <div class="role">President</div>
    </div>
    <div class="rule rule--left"></div>

    <ul class="contacts">
      <li>
        <svg viewBox="0 0 24 24" aria-hidden="true"><path d="M6.6 10.8a15.1 15.1 0 0 0 6.6 6.6l2.2-2.2c.3-.3.7-.4 1-.2 1.1.4 2.3.6 3.6.6.6 0 1 .4 1 1V20c0 .6-.4 1-1 1A17 17 0 0 1 3 4c0-.6.4-1 1-1h3.5c.6 0 1 .4 1 1 0 1.3.2 2.5.6 3.6.1.3 0 .7-.2 1l-2.3 2.2z"/></svg>
        <span>909 555 0142</span>
      </li>
      <li>
        <svg viewBox="0 0 24 24" aria-hidden="true"><path d="M6 2h12v6H6zM3 9h18a2 2 0 0 1 2 2v7h-4v4H5v-4H1v-7a2 2 0 0 1 2-2zm4 8v3h10v-3z"/></svg>
        <span>909 555 0143</span>
      </li>
      <li>
        <svg viewBox="0 0 24 24" aria-hidden="true"><path d="M2 5h20v14H2zm2 2v.5l8 5 8-5V7l-8 5z"/></svg>
        <span>daniel@orvelpantry.com</span>
      </li>
    </ul>

    <svg class="base-band" viewBox="0 0 600 40" aria-hidden="true">
      <defs>
        <linearGradient id="bandBlue" x1="0" x2="1" y1="0" y2="0">
          <stop offset="0" stop-color="#1f2f9e"/>
          <stop offset="0.6" stop-color="#2c5fc0"/>
          <stop offset="1" stop-color="#3fa6d8"/>
        </linearGradient>
      </defs>
      <polygon points="0,30 410,14 410,40 0,40" fill="url(#bandBlue)"/>
      <polygon points="416,14 600,6 600,40 416,40" fill="#4cb83a"/>
    </svg>
  </section>
</body>
</html>
```